Kestrelbrook Student Accomodation needs a business card design

Hi Guys,

We are a Student Accommodation company in Australia. We already have a logo which I will submit.

I will require the design of the business cards from you.

I am after something that looks clean, modern and that people feel interested and actually want to contact us.

We would like to see designs that are innovative.

On the business cards I will require to have:

Employee Name
Position
Phone number
Email
Facebook page

I hope you can help me with this project guys as I have heard really good things from you.

```html
<!DOCTYPE html>
<html lang="en">
<head>
<meta charset="utf-8">
<title>Kestrelbrook Stays – Business Card</title>
<link href="https://fonts.googleapis.com/css2?family=Open+Sans:wght@400;700&family=Arimo:wght@400&display=swap" rel="stylesheet">
<style>
  :root {
    --canvas: #ecebe8;
    --card-white: #ffffff;
    --brand-green: #078f47;
    --brand-gold: #f2b32c;
    --text-light: #ffffff;
    --edge: #c9c9c9;
  }
  * { margin: 0; padding: 0; box-sizing: border-box; }
  html, body { width: 1200px; height: 765px; overflow: hidden; background: var(--canvas); }
  .canvas { position: relative; width: 1200px; height: 765px; }

  .card {
    position: absolute;
    width: 560px;
    height: 320px;
    background: var(--card-white);
    border: 1px solid var(--edge);
    overflow: hidden;
  }
  .card--front { left: 60px; top: 60px; }
  .card--back { left: 580px; top: 385px; }

  .front-brand {
    height: 174px;
    display: flex;
    align-items: center;
    justify-content: center;
    gap: 14px;
  }
  .brand-square {
    width: 30px;
    height: 30px;
    background: var(--brand-gold);
  }
  .brand-name {
    font-family: "Open Sans", sans-serif;
    font-weight: 700;
    color: var(--brand-green);
    letter-spacing: 0.5px;
  }
  .front-brand .brand-name { font-size: 28px; }

  .front-details {
    position: absolute;
    left: 0; right: 0; bottom: 0;
    height: 146px;
    background: var(--brand-green);
    color: var(--text-light);
  }
  .person { position: absolute; left: 30px; top: 20px; font-family: "Open Sans", sans-serif; }
  .person-name { font-size: 19px; font-weight: 700; }
  .person-position { font-size: 15px; margin-top: 3px; }

  .divider {
    position: absolute;
    left: 272px; top: 30px;
    width: 2px; height: 72px;
    background: linear-gradient(to bottom, rgba(255,255,255,0), rgba(255,255,255,0.95) 50%, rgba(255,255,255,0));
  }

  .contacts {
    position: absolute;
    left: 305px; top: 20px;
    list-style: none;
    font-family: "Arimo", sans-serif;
    font-size: 14.5px;
  }
  .contact { display: flex; align-items: center; gap: 8px; height: 26px; }
  .contact svg { width: 12px; height: 12px; flex: none; }
  .social-square { width: 11px; height: 11px; background: var(--text-light); flex: none; }

  .card--back {
    display: flex;
    align-items: center;
    justify-content: center;
    gap: 18px;
  }
  .card--back .brand-square { width: 44px; height: 44px; }
  .card--back .brand-name { font-size: 38px; }
</style>
</head>
<body>
<main class="canvas">
  <section class="card card--front">
    <div class="front-brand">
      <span class="brand-square"></span>
      <span class="brand-name">Kestrelbrook Stays</span>
    </div>
    <div class="front-details">
      <div class="person">
        <p class="person-name">Employee Name</p>
        <p class="person-position">Position</p>
      </div>
      <span class="divider"></span>
      <ul class="contacts">
        <li class="contact">
          <svg viewBox="0 0 12 12" aria-hidden="true"><circle cx="6" cy="6" r="5.3" fill="none" stroke="#fff" stroke-width="1"/><path d="M4 3.2 L5 3 L5.6 4.6 L5 5.1 Q5.5 6.4 6.9 7 L7.4 6.4 L9 7 L8.8 8 Q6.6 8.6 4.6 6.8 Q3.2 5 4 3.2 Z" fill="#fff"/></svg>
          <span>123-456-7890</span>
        </li>
        <li class="contact">
          <svg viewBox="0 0 12 12" aria-hidden="true"><rect x="1" y="2.5" width="10" height="7" fill="#fff"/><path d="M1 2.8 L6 6.5 L11 2.8" fill="none" stroke="#078f47" stroke-width="1"/></svg>
          <span>info@kestrelbrook.com</span>
        </li>
        <li class="contact">
          <span class="social-square"></span>
          <span>/kestrelbrookstays</span>
        </li>
      </ul>
    </div>
  </section>

  <section class="card card--back">
    <span class="brand-square"></span>
    <span class="brand-name">Kestrelbrook Stays</span>
  </section>
</main>
</body>
</html>
```